Marlowick Cafe' eLiquid Label - retro, trendy design

Need a 1.5"x3" label designed for an eLiquid bottle. I like the distressed retro diner look. Feel free to take creative license on logo, images etc. Attaching a mockup I did just to give you an idea of what look I want - the attached concept has all textual elements required....want retro trendy....corvanel-ish look and personality...warm colors...high contrasts. attached Nolse image is the mockup I want redesigned.

Target Market(s)

eclectic

Industry/Entity Type

Cafe

Font styles to use
Serif
Decorative

Requirements
Must have
• text elements from uploaded sample - 1.5x3 inch high res
Nice to have
• incorporate QM logo somewhere in the design - attached

```html
<!DOCTYPE html>
<html lang="en">
<head>
<meta charset="utf-8">
<title>Marlowick Cafe' eLiquid Label</title>
<link rel="stylesheet" href="https://fonts.googleapis.com/css2?family=Cinzel:wght@600;700&family=Marcellus&family=Arimo:wght@400&family=Archivo+Narrow:wght@400&display=swap">
<style>
  :root {
    --page: #f2f0ec;
    --parchment-light: #eadcb6;
    --parchment: #dcc898;
    --parchment-dark: #c4ab76;
    --ink: #1f1a14;
    --ink-soft: #3a3024;
    --panel: #efe6d0;
    --band: #3b2b17;
    --rope: #cdbb95;
  }
  * { margin: 0; padding: 0; box-sizing: border-box; }
  html, body { width: 870px; height: 1200px; overflow: hidden; }
  body { background: var(--page); position: relative; }

  .label {
    position: absolute; left: 20px; top: 394px;
    width: 830px; height: 412px; overflow: hidden;
    background: var(--parchment);
  }
  .label__map {
    position: absolute; inset: 0;
    background:
      radial-gradient(ellipse at 40% 45%, var(--parchment-light) 0%, var(--parchment) 55%, var(--parchment-dark) 100%);
  }
  .label__rope {
    position: absolute; bottom: 14px; height: 80px;
    background: radial-gradient(ellipse at 50% 100%, var(--rope) 0%, rgba(205,187,149,0) 70%);
  }
  .label__rope--left { left: 60px; width: 160px; }
  .label__rope--right { left: 430px; width: 220px; }

  .barcode-panel {
    position: absolute; left: 0; top: 86px; width: 78px; bottom: 14px;
    background: var(--panel);
  }

  .brand-mark {
    position: absolute; left: 336px; top: 100px; width: 170px; height: 110px;
    display: flex; flex-direction: column; align-items: center; justify-content: center; gap: 6px;
  }
  .brand-mark__circle {
    width: 28px; height: 28px; border-radius: 50%; border: 3px solid var(--ink);
  }
  .brand-mark__name {
    font-family: 'Cinzel', serif; font-weight: 700; font-size: 20px;
    color: var(--ink); letter-spacing: 1px;
  }
  .brand-mark__url {
    font-family: 'Cinzel', serif; font-weight: 700; font-size: 8px;
    color: var(--ink); letter-spacing: 0.5px;
  }

  .flourish {
    position: absolute; top: 112px; height: 56px;
    background: linear-gradient(90deg, rgba(31,26,20,0) 0%, rgba(31,26,20,0.55) 50%, rgba(31,26,20,0) 100%);
    border-radius: 50%;
    opacity: 0.6;
  }
  .flourish--left { left: 212px; width: 140px; }
  .flourish--right { left: 490px; width: 134px; }

  .product-name {
    position: absolute; left: 190px; width: 460px; top: 226px;
    text-align: center;
    font-family: 'Cinzel', serif; font-weight: 700; font-size: 48px;
    letter-spacing: 4px; color: var(--ink); line-height: 1;
  }
  .rule {
    position: absolute; left: 229px; width: 390px; top: 282px;
    height: 1.5px; background: var(--ink-soft);
  }
  .origin {
    position: absolute; left: 190px; width: 460px; top: 302px;
    text-align: center;
    font-family: 'Marcellus', serif; font-size: 21px; color: var(--ink-soft);
  }
  .volume {
    position: absolute; left: 190px; width: 460px; top: 360px;
    text-align: center;
    font-family: 'Arimo', sans-serif; font-size: 19px; color: var(--ink);
  }

  .info-panel {
    position: absolute; left: 676px; top: 0; width: 154px; bottom: 14px;
    background: var(--panel);
    display: flex; justify-content: center; padding: 14px 10px;
  }
  .info-panel__text {
    writing-mode: vertical-rl; transform: rotate(180deg);
    font-family: 'Archivo Narrow', sans-serif; font-size: 11.5px; line-height: 1.35;
    color: var(--ink);
  }
  .info-panel__text p + p { margin-right: 10px; }
  .info-panel__text .gap { margin-right: 18px; }

  .label__band {
    position: absolute; left: 0; right: 0; bottom: 0; height: 14px;
    background: var(--band);
  }
</style>
</head>
<body>
  <section class="label">
    <div class="label__map" role="img" aria-label="Faded antique world map background in parchment tones"></div>
    <div class="label__rope label__rope--left" role="img" aria-label="Coiled rope and compass rose along the lower left"></div>
    <div class="label__rope label__rope--right" role="img" aria-label="Coiled rope along the lower edge"></div>

    <div class="barcode-panel"></div>

    <div class="flourish flourish--left" role="img" aria-label="Decorative scroll flourish"></div>
    <div class="flourish flourish--right" role="img" aria-label="Decorative scroll flourish"></div>

    <div class="brand-mark">
      <span class="brand-mark__circle"></span>
      <span class="brand-mark__name">Marlowick</span>
      <span class="brand-mark__url">WWW.MARLOWICKVAPOR.COM</span>
    </div>

    <h1 class="product-name">TIRAMISU</h1>
    <div class="rule"></div>
    <p class="origin">Made in USA</p>
    <p class="volume">12 mL</p>

    <aside class="info-panel">
      <div class="info-panel__text">
        <p>Vegetable Glycerin, Propylene Glycol, Flavoring, Nicotine</p>
        <p class="gap">PROP 64: KEEP OUT OF CHILDREN AND PETS. NPHC POISON HOTLINE: 800-555-0142. NICOTIN IS A CHEMICAL KNOWN IN THE STATE OF CALIFORNIA</p>
        <p class="gap">TO CAUSE BIRTH DEFECTS AND OFFER REPROODUCTIVE HARM NICOTINE IS AN ADDICTIVE CHEMICAL DEERIVES FROM TOBACO. 8+ ONYLY</p>
      </div>
    </aside>

    <div class="label__band"></div>
  </section>
</body>
</html>
```